Agriculture Business Card

I want to use my existing logo and use my tagline of "Don't Guess...Soil Test" on the card. Looking for a double sided card that will really get peoples attention.
Contact Info:
Marlow Field Crop Edge
Calvin Brusk
2917 K Lane
Larkin, NE 68593
402-555-0193
calvin.r.brusk@fieldmailbox.net

```html
<!DOCTYPE html>
<html lang="en">
<head>
<meta charset="utf-8">
<title>Marlow Field Crop Edge – Business Card</title>
<link rel="stylesheet" href="https://fonts.googleapis.com/css2?family=Roboto+Condensed:wght@700&family=Roboto:ital,wght@0,400;1,700&display=swap">
<style>
  :root {
    --page: #e4e4e4;
    --card-white: #ffffff;
    --brown: #7a4a2e;
    --brown-deep: #7a4429;
    --brown-light: #a8735a;
    --orange: #f5a21c;
    --green: #5cb848;
    --green-deep: #35a332;
    --text-grey: #4a4a4a;
    --corn-faint: #fbe3b0;
    --leaf-faint: #d6ecd0;
  }
  * { box-sizing: border-box; margin: 0; padding: 0; }
  html, body { width: 1200px; height: 1200px; overflow: hidden; }
  body {
    background: var(--page);
    display: flex;
    flex-direction: column;
    align-items: center;
    justify-content: center;
    gap: 60px;
    font-family: "Roboto", Arial, sans-serif;
  }
  .card {
    position: relative;
    width: 880px;
    height: 503px;
    border-radius: 28px;
    overflow: hidden;
  }
  .card-front { background: var(--card-white); }
  .card-back {
    background: linear-gradient(200deg, var(--brown-light) 0%, #935f43 50%, var(--brown-deep) 100%);
  }

  /* faint decorative crop illustration area */
  .front-decoration {
    position: absolute;
    left: 0; top: 40px;
    width: 420px; height: 463px;
    background:
      radial-gradient(ellipse 110px 170px at 190px 110px, var(--corn-faint) 0%, rgba(251,227,176,0) 100%),
      radial-gradient(ellipse 90px 140px at 380px 330px, var(--corn-faint) 0%, rgba(251,227,176,0) 100%),
      radial-gradient(ellipse 180px 260px at 80px 360px, var(--leaf-faint) 0%, rgba(214,236,208,0) 100%);
    opacity: .85;
  }

  .brand-block {
    position: absolute;
    left: 590px; top: 60px;
    width: 240px;
    display: flex;
    flex-direction: column;
    align-items: center;
    gap: 22px;
  }
  .brand-dot {
    width: 120px; height: 120px;
    border-radius: 50%;
    background: var(--orange);
  }
  .brand-name {
    font-family: "Roboto Condensed", "Arial Narrow", sans-serif;
    font-weight: 700;
    font-size: 30px;
    line-height: 1.1;
    color: var(--brown-light);
    text-align: center;
  }

  .person-name {
    position: absolute;
    left: 55px; top: 286px;
    font-family: "Roboto Condensed", "Arial Narrow", sans-serif;
    font-weight: 700;
    font-size: 48px;
    letter-spacing: .5px;
    color: var(--brown);
  }

  .divider {
    position: absolute;
    left: 55px; top: 380px;
    width: 770px; height: 8px;
    display: flex; gap: 5px;
  }
  .divider span { flex: 1; }
  .divider .seg-orange { background: var(--orange); }
  .divider .seg-green { background: var(--green); }
  .divider .seg-green-deep { background: var(--green-deep); }
  .divider .seg-green-soft { background: #72c25a; }

  .contact {
    position: absolute;
    left: 55px; top: 410px;
    font-size: 20px;
    line-height: 26px;
    color: var(--text-grey);
  }
  .contact li { list-style: none; display: flex; align-items: center; gap: 9px; }
  .contact svg { width: 16px; height: 16px; fill: var(--brown); }

  .address {
    position: absolute;
    right: 55px; top: 410px;
    font-size: 20px;
    line-height: 26px;
    color: var(--text-grey);
    text-align: right;
    font-style: normal;
  }

  .back-brand {
    position: absolute;
    left: 0; right: 0; top: 110px;
    display: flex;
    flex-direction: column;
    align-items: center;
    gap: 26px;
  }
  .back-brand .brand-dot { width: 150px; height: 150px; }
  .back-brand .brand-name { color: var(--orange); font-size: 40px; }

  .tagline {
    position: absolute;
    left: 0; right: 0; top: 408px;
    text-align: center;
    font-family: "Roboto", Arial, sans-serif;
    font-style: italic;
    font-weight: 700;
    font-size: 35px;
    letter-spacing: .5px;
  }
  .tagline .lead { color: var(--green-deep); }
  .tagline .close { color: var(--orange); }
</style>
</head>
<body>
  <section class="card card-front">
    <div class="front-decoration" role="img" aria-label="Faint illustration of a corn cob with leaves and a flexed arm"></div>

    <div class="brand-block">
      <div class="brand-dot"></div>
      <p class="brand-name">Marlow Field<br>Crop Edge</p>
    </div>

    <h1 class="person-name">CALVIN BRUSK</h1>

    <div class="divider">
      <span class="seg-orange"></span>
      <span class="seg-green"></span>
      <span class="seg-green-deep"></span>
      <span class="seg-green-soft"></span>
    </div>

    <ul class="contact">
      <li>
        <svg viewBox="0 0 24 24" aria-hidden="true"><path d="M6.6 10.8a15.1 15.1 0 0 0 6.6 6.6l2.2-2.2a1 1 0 0 1 1-.25 11.4 11.4 0 0 0 3.6.57 1 1 0 0 1 1 1V20a1 1 0 0 1-1 1A17 17 0 0 1 3 4a1 1 0 0 1 1-1h3.5a1 1 0 0 1 1 1c0 1.25.2 2.45.57 3.57a1 1 0 0 1-.25 1z"/></svg>
        402-555-0193
      </li>
      <li>
        <svg viewBox="0 0 24 24" aria-hidden="true"><path d="M2 5h20v14H2z M3.5 6.5 12 13l8.5-6.5" stroke="#fff" stroke-width="1.6"/></svg>
        calvin.r.brusk@fieldmailbox.net
      </li>
    </ul>

    <address class="address">
      2917 K Lane<br>
      Larkin, NE 68593
    </address>
  </section>

  <section class="card card-back">
    <div class="back-brand">
      <div class="brand-dot"></div>
      <p class="brand-name">Marlow Field Crop Edge</p>
    </div>
    <p class="tagline"><span class="lead">DON'T GUESS...</span><span class="close">SOIL TEST</span></p>
  </section>
</body>
</html>
```